Capability statement. I’ll send through what I put into Orvix. Once layout is sorted I can send through more images

Target Market(s)

Tier 1 and 2 contractors

Industry/Entity Type

Civil construction

Colors
00AB8E
00BBA5
67D7C9
C6EFE9
E9F9F6

Requirements
Must have
• Black backgrounds and Matt charcoal/aqua colour scheme

```html
<!DOCTYPE html>
<html lang="en">
<head>
<meta charset="utf-8">
<title>Kestrel Civil Group – Capability Statement</title>
<link href="https://fonts.googleapis.com/css2?family=Russo+One&family=Poppins:wght@400;500;600&display=swap" rel="stylesheet">
<style>
:root{
  --teal:#00AB8E;
  --teal-bright:#00BBA5;
  --teal-soft:#67D7C9;
  --teal-pale:#C6EFE9;
  --teal-mist:#E9F9F6;
  --black:#050606;
  --charcoal:#121716;
  --charcoal-teal:#1b3330;
  --line:#2e3534;
  --white:#ffffff;
}
*{margin:0;padding:0;box-sizing:border-box}
html,body{width:1200px;height:576px;overflow:hidden;background:#fff}
body{position:relative;font-family:"Poppins",sans-serif;color:var(--white)}
.page{position:absolute;top:26px;width:372px;height:525px;background:var(--black);overflow:hidden}
.page--cover{left:32px}
.page--stormwater{left:416px}
.page--earthworks{left:799px}
.abs{position:absolute}
.heading{font-family:"Russo One",sans-serif;text-transform:uppercase;line-height:1;letter-spacing:.3px}
.heading .accent{color:var(--teal-bright)}

/* brand mark */
.brand{position:absolute;font-family:"Poppins",sans-serif;font-weight:600;color:#8a9190;line-height:1;text-transform:uppercase}
.brand__name{display:block;letter-spacing:.5px}
.brand__sub{display:block;letter-spacing:2px}
.brand--small{right:10px;top:10px;text-align:left}
.brand--small .brand__name{font-size:13px}
.brand--small .brand__sub{font-size:5px;margin-top:2px}

/* cover */
.cover-art{position:absolute;left:0;top:0}
.cover .brand{left:8px;top:286px}
.cover .brand__name{font-size:26px}
.cover .brand__sub{font-size:8px;letter-spacing:3px;margin-top:3px}
.cover-title{left:8px;top:340px;font-size:25px}
.cover-title span{display:block;margin-bottom:3px}
.cover-intro{left:8px;top:396px;font-size:7.6px;line-height:12.5px;width:190px}
.cover-intro b{color:var(--teal-bright);font-weight:600}
.strength{position:absolute;display:flex;align-items:center;gap:6px;font-size:6.6px;font-weight:600;line-height:10px;text-transform:uppercase}
.strength svg{width:22px;height:22px}
.service{position:absolute;left:253px;display:flex;align-items:center;gap:10px;font-size:7.4px;font-weight:600;line-height:10px;text-transform:uppercase}
.service__icon{width:35px;height:35px;border-radius:50%;background:#0c1110;display:flex;align-items:center;justify-content:center}
.service__icon svg{width:18px;height:18px}

/* inner pages */
.page-title{left:8px;top:6px;font-size:20px}
.page-title span{display:block;margin-bottom:1.5px}
.page-intro{left:8px;font-size:7.6px;line-height:12.5px}
.photo-card{position:absolute;overflow:hidden}
.photo-card .photo{width:100%}
.photo-card .caption{position:absolute;left:0;right:0;bottom:0;background:var(--teal-bright);font-size:5.8px;font-weight:600;line-height:7.5px;text-transform:uppercase;padding:5px 8px;color:#062b26}
.caps-title{left:0;width:372px;text-align:center;top:274px;font-size:20px}
.caps-title span{display:block;margin-bottom:2px}
.node{position:absolute;width:80px;margin-left:-40px;text-align:center}
.node__dot{width:35px;height:35px;margin:0 auto;border-radius:50%;background:var(--teal);display:flex;align-items:center;justify-content:center}
.node__dot svg{width:19px;height:19px}
.node__label{font-size:7.4px;font-weight:500;line-height:10px;margin-top:4px}
.footer{position:absolute;left:0;right:0;bottom:0;height:22px;background:linear-gradient(90deg,#0b1513,#142624 60%,#0b1513);display:flex;align-items:center;justify-content:space-between;padding:0 8px;font-size:6.3px;color:#cfd6d4}
.footer__num{position:absolute;left:50%;transform:translateX(-50%);font-weight:600}
.hero-photo{position:absolute;right:0;top:110px;width:230px;height:310px;background:radial-gradient(ellipse at 60% 45%,#5d8c8c 0%,#3c5e5a 35%,#15231f 70%,rgba(5,6,6,0) 100%)}
.checklist{position:absolute;top:426px;font-size:7.4px;line-height:16.2px;list-style:none}
.checklist li{display:flex;align-items:center;gap:4px}
.checklist svg{width:8px;height:8px;flex:none}
</style>
</head>
<body>

<!-- Page 1: cover -->
<section class="page page--cover cover">
  <svg class="cover-art" width="372" height="525" viewBox="0 0 372 525">
    <defs>
      <linearGradient id="sky" x1="0" y1="0" x2="0" y2="1">
        <stop offset="0" stop-color="#4d5f74"/>
        <stop offset=".28" stop-color="#c9907e"/>
        <stop offset=".42" stop-color="#2c3a2a"/>
        <stop offset=".6" stop-color="#2fa8a0"/>
        <stop offset=".78" stop-color="#8a8074"/>
        <stop offset="1" stop-color="#5d5145"/>
      </linearGradient>
      <linearGradient id="sidePanel" x1="0" y1="0" x2="1" y2="1">
        <stop offset="0" stop-color="#1f3b37"/>
        <stop offset="1" stop-color="#0b1312"/>
      </linearGradient>
    </defs>
    <rect width="372" height="525" fill="var(--black)"/>
    <rect width="372" height="330" fill="url(#sky)" role="img" aria-label="Photo: teal excavator on a cleared civil site at sunset"/>
    <path d="M372 232 L372 525 L214 525 L214 300 Q214 286 228 283 Z" fill="url(#sidePanel)"/>
    <path d="M0 168 L170 275 Q190 290 200 305 L0 305 Z" fill="var(--teal)"/>
    <path d="M0 206 L168 292 Q200 305 214 300 L214 525 L0 525 Z" fill="var(--black)"/>
    <path d="M214 300 Q214 286 228 283 L372 232 L372 240 L228 292 Q222 294 222 304 L222 525 L214 525 Z" fill="#0c1514"/>
  </svg>

  <div class="brand"><span class="brand__name">Kestrel</span><span class="brand__sub">Civil Group</span></div>
  <h1 class="abs heading cover-title"><span>Capability</span><span class="accent">Statement</span></h1>
  <p class="abs cover-intro">Delivering Civil Infrastructure, Earthworks and Drainage Solutions <b>Across NSW</b></p>

  <div class="strength" style="left:10px;top:464px">
    <svg viewBox="0 0 24 24" fill="none" stroke="var(--teal-bright)" stroke-width="1.4"><circle cx="7" cy="9" r="2.5"/><circle cx="17" cy="9" r="2.5"/><circle cx="12" cy="13" r="2.5"/><path d="M3 20c0-3 2-5 4-5M21 20c0-3-2-5-4-5M7 22c0-3 2-5 5-5s5 2 5 5"/></svg>
    <span>Experienced<br>Team</span></div>
  <div class="strength" style="left:104px;top:464px">
    <svg viewBox="0 0 24 24" fill="none" stroke="var(--teal-bright)" stroke-width="1.4"><rect x="3" y="13" width="13" height="6" rx="1"/><path d="M8 13V9h5l3 4M16 11l4-5 2 1-3 6"/><circle cx="6" cy="20" r="1.5"/><circle cx="13" cy="20" r="1.5"/></svg>
    <span>Modern<br>Fleet</span></div>
  <div class="strength" style="left:10px;top:502px">
    <svg viewBox="0 0 24 24" fill="none" stroke="var(--teal-bright)" stroke-width="1.4"><path d="M12 2l8 3v6c0 5-4 9-8 11-4-2-8-6-8-11V5z"/><path d="M8 12l3 3 5-6"/></svg>
    <span>Safety<br>Focused</span></div>
  <div class="strength" style="left:104px;top:502px">
    <svg viewBox="0 0 24 24" fill="none" stroke="var(--teal-bright)" stroke-width="1.4"><circle cx="12" cy="12" r="9"/><circle cx="12" cy="12" r="5"/><circle cx="12" cy="12" r="1.5"/><path d="M12 12l8-8M17 3v4h4"/></svg>
    <span>Proven<br>Delivery</span></div>

  <div class="service" style="top:300px"><span class="service__icon"><svg viewBox="0 0 24 24" fill="var(--teal-bright)"><path d="M2 20h20v2H2zM4 14l5-3 3 4H4zM13 8l6-5 2 2-5 6z"/><rect x="10" y="10" width="5" height="4"/></svg></span><span>Bulk<br>Earthworks</span></div>
  <div class="service" style="top:345px"><span class="service__icon"><svg viewBox="0 0 24 24" fill="var(--teal-bright)"><rect x="3" y="16" width="14" height="4" rx="2"/><rect x="5" y="11" width="8" height="5"/><path d="M13 12l5-8 3 2-4 7z"/></svg></span><span>Detailed<br>Excavation</span></div>
  <div class="service" style="top:390px"><span class="service__icon"><svg viewBox="0 0 24 24" fill="var(--teal-bright)"><rect x="4" y="4" width="4" height="10"/><rect x="9" y="8" width="4" height="6"/><path d="M2 17q5-3 10 0t10 0v3q-5 3-10 0t-10 0z"/></svg></span><span>Drainage</span></div>
  <div class="service" style="top:436px"><span class="service__icon"><svg viewBox="0 0 24 24" fill="var(--teal-bright)"><path d="M9 3h2l-1 18H4zM13 3h2l5 18h-6z"/><rect x="11.3" y="5" width="1.4" height="3"/><rect x="11.3" y="11" width="1.4" height="3"/><rect x="11.3" y="17" width="1.4" height="3"/></svg></span><span>Roadworks</span></div>
  <div class="service" style="top:482px"><span class="service__icon"><svg viewBox="0 0 24 24" fill="var(--teal-bright)"><path d="M6 4h5l2 8H5z"/><rect x="3" y="13" width="18" height="5"/><rect x="2" y="19" width="20" height="2"/></svg></span><span>Plant Hire</span></div>
</section>

<!-- Page 2: stormwater -->
<section class="page page--stormwater">
  <h2 class="abs heading page-title"><span>Stormwater</span><span>and Civil</span><span class="accent">Infrastructure</span></h2>
  <div class="brand brand--small"><span class="brand__name">Kestrel</span><span class="brand__sub">Civil Group</span></div>
  <p class="abs page-intro" style="top:77px">Delivering complex drainage, utility and civil<br>infrastructure solutions across NSW</p>

  <div class="photo-card" style="left:7.5px;top:118px;width:85px;height:122px">
    <div class="photo" role="img" aria-label="Photo: deep drainage trench with shoring box" style="height:98px;background:linear-gradient(180deg,#8fa9a6,#6b5f4e 45%,#8b3a3a 80%,#4a3a2c)"></div>
    <div class="caption">Deep Drainage Installation</div></div>
  <div class="photo-card" style="left:98px;top:118px;width:85px;height:122px">
    <div class="photo" role="img" aria-label="Photo: lined retention basin under blue sky" style="height:98px;background:linear-gradient(180deg,#2f6fb4,#86a6c8 30%,#c79a58 45%,#d9dde2 70%,#9aa3ab)"></div>
    <div class="caption">Retention Basins</div></div>
  <div class="photo-card" style="left:188.5px;top:118px;width:85px;height:122px">
    <div class="photo" role="img" aria-label="Photo: utility and service trench through grassland" style="height:98px;background:linear-gradient(180deg,#6f7a6d,#4f5b44 35%,#555a52 70%,#3f4a36)"></div>
    <div class="caption">Utility &amp; Service Trenches</div></div>
  <div class="photo-card" style="left:279px;top:118px;width:85px;height:122px">
    <div class="photo" role="img" aria-label="Photo: headwall and outlet pipes with rock beaching" style="height:98px;background:linear-gradient(180deg,#c9d6e0,#8aa 35%,#3a3f42 50%,#d8d6d0 75%,#9b9892)"></div>
    <div class="caption">Headwalls &amp; Outlet Structures</div></div>

  <svg class="abs" style="left:0;top:0" width="372" height="525" viewBox="0 0 372 525" fill="none" stroke="var(--line)" stroke-width="1.2">
    <path d="M-4 292 Q186 440 376 292"/>
    <path d="M-4 368 Q186 520 376 368"/>
  </svg>

  <h2 class="abs heading caps-title"><span>Our</span><span>Capabilities</span></h2>

  <div class="node" style="left:30px;top:302px"><div class="node__dot"><svg viewBox="0 0 24 24" fill="#fff"><rect x="4" y="4" width="3" height="8"/><rect x="8" y="7" width="3" height="5"/><path d="M2 14q5-3 10 0t10 0v2q-5 3-10 0t-10 0zM2 18q5-3 10 0t10 0v2q-5 3-10 0t-10 0z"/></svg></div><div class="node__label">Stormwater<br>Drainage</div></div>
  <div class="node" style="left:101px;top:332px"><div class="node__dot"><svg viewBox="0 0 24 24" fill="none" stroke="#fff" stroke-width="2"><rect x="5" y="7" width="14" height="12" rx="2"/><circle cx="12" cy="13" r="3"/><path d="M9 7V3h6v4"/></svg></div><div class="node__label">RRJ Pipe<br>Installation</div></div>
  <div class="node" style="left:178px;top:347px"><div class="node__dot"><svg viewBox="0 0 24 24" fill="none" stroke="#fff" stroke-width="2"><circle cx="12" cy="12" r="8"/><path d="M9 15l6-6M14 7l3 3"/></svg></div><div class="node__label" style="margin-top:8px">Orvix Installation</div></div>
  <div class="node" style="left:263px;top:332px"><div class="node__dot"><svg viewBox="0 0 24 24" fill="none" stroke="#fff" stroke-width="2"><rect x="4" y="4" width="16" height="16" rx="2"/><path d="M8 8h8v8H8zM12 8v8M8 12h8"/></svg></div><div class="node__label">Junction Pits &amp;<br>Manholes</div></div>
  <div class="node" style="left:339px;top:302px"><div class="node__dot"><svg viewBox="0 0 24 24" fill="none" stroke="#fff" stroke-width="2"><path d="M12 21s-5-6-5-10a5 5 0 0110 0c0 4-5 10-5 10z"/><circle cx="12" cy="11" r="1.8"/><path d="M3 9a6 6 0 013-4M21 9a6 6 0 00-3-4"/></svg></div><div class="node__label">Utility<br>Relocations</div></div>
  <div class="node" style="left:30px;top:378px"><div class="node__dot"><svg viewBox="0 0 24 24" fill="none" stroke="#fff" stroke-width="2"><path d="M3 6v12h18V6"/><path d="M5 10q3.5-2 7 0t7 0"/></svg></div><div class="node__label">Retention<br>Basins</div></div>
  <div class="node" style="left:101px;top:408px"><div class="node__dot"><svg viewBox="0 0 24 24" fill="none" stroke="#fff" stroke-width="2"><path d="M4 20V10a8 8 0 0116 0v10"/><path d="M8 20v-9a4 4 0 018 0v9"/></svg></div><div class="node__label">Headwalls<br>&amp; Culverts</div></div>
  <div class="node" style="left:178px;top:422px"><div class="node__dot"><svg viewBox="0 0 24 24" fill="#fff"><rect x="3" y="15" width="12" height="4" rx="2"/><rect x="5" y="10" width="7" height="5"/><path d="M12 11l5-7 3 2-4 6z"/></svg></div><div class="node__label" style="margin-top:8px">Deep Excavation</div></div>
  <div class="node" style="left:263px;top:408px"><div class="node__dot"><svg viewBox="0 0 24 24" fill="#fff"><path d="M4 13a8 8 0 0116 0z"/><rect x="3" y="13" width="18" height="2"/><path d="M7 17h10l-1 4H8z"/></svg></div><div class="node__label">Civil<br>Infrastructure</div></div>
  <div class="node" style="left:339px;top:378px"><div class="node__dot"><svg viewBox="0 0 24 24" fill="none" stroke="#fff" stroke-width="2"><path d="M10 21v-9a1.5 1.5 0 013 0v4l4 1v4"/><path d="M7 8a5 5 0 0110 0"/></svg></div><div class="node__label">GPS Controlled<br>Excavation</div></div>

  <footer class="footer"><span>www.kestrelcivil.com.au</span><span class="footer__num">02</span><span>Kestrel Civil Group &nbsp;|&nbsp; Capability Statement</span></footer>
</section>

<!-- Page 3: earthworks -->
<section class="page page--earthworks">
  <div class="hero-photo" role="img" aria-label="Photo: teal excavator lifting soil against bushland"></div>
  <h2 class="abs heading page-title"><span>Bulk Earthworks &amp;</span><span class="accent">Subdivision Development</span></h2>
  <div class="brand brand--small"><span class="brand__name">Kestrel</span><span class="brand__sub">Civil Group</span></div>
  <p class="abs page-intro" style="top:53px">Delivering large-scale earthworks, road formation, cut-to-fill operations and<br>subdivision infrastructure projects across NSW.</p>

  <div class="photo-card" style="left:7.5px;top:98px;width:175.5px;height:123px">
    <div class="photo" role="img" aria-label="Photo: detailed excavation benches on a cut-to-fill site" style="height:98px;background:linear-gradient(180deg,#5a8cc4,#a9c3da 30%,#8d7a5e 45%,#9a4f30 70%,#b8876a)"></div>
    <div class="caption" style="text-align:center">Detailed Excavation &amp;<br>Cut-to-Fill Operations</div></div>
  <div class="photo-card" style="left:7.5px;top:224px;width:85px;height:123px">
    <div class="photo" role="img" aria-label="Photo: water-dampened excavation for dust suppression" style="height:98px;background:linear-gradient(180deg,#4d86c8,#9fb9d2 30%,#8c6a4a 50%,#7b4a32)"></div>
    <div class="caption">Dust Suppression &amp; Compaction Support</div></div>
  <div class="photo-card" style="left:98px;top:224px;width:85px;height:123px">
    <div class="photo" role="img" aria-label="Photo: aerial view of excavator loading a dump truck" style="height:98px;background:linear-gradient(160deg,#a28f7a,#c6b29a 40%,#8f7b66)"></div>
    <div class="caption">Subdivision Infrastructure</div></div>

  <h2 class="abs heading" style="left:8px;top:371px;font-size:20px;line-height:1.06">Earthworks<br>Capabilities</h2>

  <ul class="checklist" style="left:8px">
    <li><svg viewBox="0 0 10 10" fill="none" stroke="var(--teal-bright)" stroke-width="1"><circle cx="5" cy="5" r="4.3"/><path d="M3 5l1.5 1.5L7 3.8"/></svg>Bulk Earthworks</li>
    <li><svg viewBox="0 0 10 10" fill="none" stroke="var(--teal-bright)" stroke-width="1"><circle cx="5" cy="5" r="4.3"/><path d="M3 5l1.5 1.5L7 3.8"/></svg>GPS Machine Control</li>
    <li><svg viewBox="0 0 10 10" fill="none" stroke="var(--teal-bright)" stroke-width="1"><circle cx="5" cy="5" r="4.3"/><path d="M3 5l1.5 1.5L7 3.8"/></svg>Cut &amp; Fill Operations</li>
  </ul>
  <ul class="checklist" style="left:137px">
    <li><svg viewBox="0 0 10 10" fill="none" stroke="var(--teal-bright)" stroke-width="1"><circle cx="5" cy="5" r="4.3"/><path d="M3 5l1.5 1.5L7 3.8"/></svg>Detailed Excavation</li>
    <li><svg viewBox="0 0 10 10" fill="none" stroke="var(--teal-bright)" stroke-width="1"><circle cx="5" cy="5" r="4.3"/><path d="M3 5l1.5 1.5L7 3.8"/></svg>Rock Excavation</li>
    <li><svg viewBox="0 0 10 10" fill="none" stroke="var(--teal-bright)" stroke-width="1"><circle cx="5" cy="5" r="4.3"/><path d="M3 5l1.5 1.5L7 3.8"/></svg>Road Formation</li>
    <li><svg viewBox="0 0 10 10" fill="none" stroke="var(--teal-bright)" stroke-width="1"><circle cx="5" cy="5" r="4.3"/><path d="M3 5l1.5 1.5L7 3.8"/></svg>Final Trim</li>
  </ul>
  <ul class="checklist" style="left:257px">
    <li><svg viewBox="0 0 10 10" fill="none" stroke="var(--teal-bright)" stroke-width="1"><circle cx="5" cy="5" r="4.3"/><path d="M3 5l1.5 1.5L7 3.8"/></svg>Retention Basins</li>
    <li><svg viewBox="0 0 10 10" fill="none" stroke="var(--teal-bright)" stroke-width="1"><circle cx="5" cy="5" r="4.3"/><path d="M3 5l1.5 1.5L7 3.8"/></svg>Subdivision Development</li>
    <li><svg viewBox="0 0 10 10" fill="none" stroke="var(--teal-bright)" stroke-width="1"><circle cx="5" cy="5" r="4.3"/><path d="M3 5l1.5 1.5L7 3.8"/></svg>Water Cart Services</li>
    <li><svg viewBox="0 0 10 10" fill="none" stroke="var(--teal-bright)" stroke-width="1"><circle cx="5" cy="5" r="4.3"/><path d="M3 5l1.5 1.5L7 3.8"/></svg>Plant Hire</li>
  </ul>

  <footer class="footer"><span>www.kestrelcivil.com.au</span><span class="footer__num">03</span><span>Kestrel Civil Group &nbsp;|&nbsp; Capability Statement</span></footer>
</section>

</body>
</html>
```